Looking for a modern, Professional business card design

We have a simple business card, but are looking for a more modern, professional look. A sample of the basic card is attached as well as the logo. We would also like to add that we offer:
Struggling with your finances?
- Learn to become debt free
- Discover the power of cash
- Control your money instead of it controlling you
Let us help you achieve a new level of financial freedom!
Also, we would like to have a "SPECIAL OFFER!: FREE 30 minute consultation"
Financial Planning

```html
<!DOCTYPE html>
<html lang="en">
<head>
<meta charset="utf-8">
<title>Clearway Money Coaching – Business Card</title>
<link href="https://fonts.googleapis.com/css2?family=Open+Sans:wght@400;600;700;800&display=swap" rel="stylesheet">
<style>
  :root {
    --green-deep: #2f8a2a;
    --green-mid: #55ad34;
    --green-light: #a9d65a;
    --ink: #333333;
    --white: #ffffff;
    --backdrop: #e9ebe6;
  }
  * { box-sizing: border-box; margin: 0; padding: 0; }
  html, body { width: 1200px; height: 843px; overflow: hidden; }
  body {
    background: var(--backdrop);
    font-family: "Open Sans", Arial, sans-serif;
    display: flex;
    flex-direction: column;
    align-items: center;
    justify-content: center;
    gap: 46px;
  }
  .card {
    position: relative;
    width: 620px;
    height: 354px;
    border-radius: 18px;
    overflow: hidden;
    box-shadow: 0 6px 18px rgba(0,0,0,0.18);
  }

  /* ---------- back side ---------- */
  .card--back {
    background: radial-gradient(ellipse at 62% 45%, var(--green-light) 0%, var(--green-mid) 45%, var(--green-deep) 100%);
    color: var(--white);
    padding: 40px 40px;
  }
  .card--back .decor {
    position: absolute;
    right: -30px; top: -20px;
    width: 300px; height: 300px;
    border-radius: 50%;
    background: radial-gradient(circle, rgba(255,255,255,0.14), rgba(255,255,255,0) 70%);
  }
  .pitch__title { font-weight: 700; font-size: 17px; letter-spacing: .2px; }
  .pitch__list { list-style: none; margin-top: 4px; }
  .pitch__list li { font-size: 15px; font-style: italic; line-height: 1.35; padding-left: 18px; position: relative; }
  .pitch__list li::before { content: ""; position: absolute; left: 2px; top: 8px; width: 7px; height: 7px; border-radius: 50%; background: var(--white); }
  .pitch__close { font-size: 15px; font-style: italic; margin-top: 8px; }
  .offer__title { font-weight: 800; font-size: 22px; margin-top: 14px; }
  .offer__text { font-size: 15px; font-weight: 600; }
  .back-brand { margin-top: 14px; font-weight: 800; font-size: 34px; letter-spacing: 1px; text-transform: uppercase; color: var(--white); line-height: 1; }
  .back-brand__sub { font-size: 11px; margin-top: 4px; opacity: .85; }

  /* ---------- front side ---------- */
  .card--front { background: var(--white); }
  .front__band { position: absolute; inset: 0; }
  .brand {
    position: absolute; left: 40px; top: 44px;
    display: flex; align-items: center; gap: 14px;
  }
  .brand__dot { width: 46px; height: 46px; border-radius: 50%; background: var(--green-mid); }
  .brand__name { font-weight: 800; font-size: 30px; color: var(--ink); text-transform: uppercase; line-height: 1; }
  .brand__tag { position: absolute; left: 100px; top: 96px; font-size: 10px; font-style: italic; color: #666; }
  .contact { position: absolute; left: 36px; top: 176px; color: var(--white); }
  .contact__name { font-size: 21px; font-weight: 600; }
  .contact__role { font-size: 17px; margin-bottom: 10px; }
  .contact__line { display: flex; align-items: center; gap: 10px; font-size: 15px; line-height: 1.55; }
  .contact__line svg { width: 14px; height: 14px; flex: none; }
  .front__decor {
    position: absolute; right: 30px; bottom: 24px;
    width: 150px; height: 130px; border-radius: 50%;
    background: radial-gradient(ellipse, rgba(85,173,52,0.55), rgba(85,173,52,0) 70%);
  }
</style>
</head>
<body>

  <section class="card card--back">
    <div class="decor" role="img" aria-label="Faint brand symbol decoration"></div>
    <h2 class="pitch__title">STRUGGLING WITH YOUR FINANCES?</h2>
    <ul class="pitch__list">
      <li>Learn to become debt free</li>
      <li>Discover the power of cash</li>
      <li>Control your money instead of it controlling you</li>
    </ul>
    <p class="pitch__close">Let us help you achieve a new level of financial freedom!</p>
    <p class="offer__title">SPECIAL OFFER!</p>
    <p class="offer__text">FREE 30 minute consultation</p>
    <p class="back-brand">Clearway</p>
    <p class="back-brand__sub">Achieve a new level of personal freedom</p>
  </section>

  <section class="card card--front">
    <svg class="front__band" viewBox="0 0 620 354" preserveAspectRatio="none" aria-hidden="true">
      <defs>
        <linearGradient id="bandFill" x1="0" y1="0" x2="1" y2="0">
          <stop offset="0" stop-color="#2f8a2a"/>
          <stop offset="0.45" stop-color="#7cc23f"/>
          <stop offset="1" stop-color="#ffffff"/>
        </linearGradient>
      </defs>
      <path d="M0 150 Q300 135 620 185 L620 354 L0 354 Z" fill="url(#bandFill)"/>
    </svg>

    <div class="brand">
      <span class="brand__dot"></span>
      <span class="brand__name">Clearway Money Coaching</span>
    </div>
    <p class="brand__tag">Achieve a new level of personal freedom</p>

    <div class="contact">
      <p class="contact__name">Daniel R. Hayes</p>
      <p class="contact__role">Personal Financial Coach</p>
      <p class="contact__line">
        <svg viewBox="0 0 14 14"><rect x="3" y="1" width="8" height="12" rx="1.5" fill="none" stroke="#fff" stroke-width="1.4"/><circle cx="7" cy="11" r=".8" fill="#fff"/></svg>
        (205) 555-0182
      </p>
      <p class="contact__line">
        <svg viewBox="0 0 14 14"><rect x="1" y="3" width="12" height="8" fill="#fff"/><path d="M1 3 L7 8 L13 3" fill="none" stroke="#55ad34" stroke-width="1"/></svg>
        daniel@clearwaymoney.com
      </p>
      <p class="contact__line">
        <svg viewBox="0 0 14 14"><circle cx="7" cy="7" r="6" fill="#fff"/><path d="M1 7 H13 M7 1 Q3 7 7 13 Q11 7 7 1" fill="none" stroke="#55ad34" stroke-width="1"/></svg>
        www.clearwaymoney.com
      </p>
    </div>

    <div class="front__decor" role="img" aria-label="Brand symbol decoration area"></div>
  </section>

</body>
</html>
```